Moulding supply company needs a Door Hanger Design

Door Hanger Design Request from Loft Crafta
www. loftcraftas.ca
We are moulding factory outlet in Toronto. Provide high quality moulding materials with competitive price like crown mouldings, casings, wainscoting, flatstocks, baseboards. We also provide professional installation for our clients. This door hanger will help the home owner easily find a local factory supplier with providing the materials as well as installation.

Detail request for design:
Size: 4”x11”, vertical
Shape: Rectangle

Content:
Front
1. Logo, see attachment(Use the left one, horizontal one)
2. Moulding factory outlet direct sale
3. Supply high quality Crown mouldings, baseboards, casings and wainscotings with competitive price
4. Installation & delivery
#2 content is the most important content, should be bold and readable
#3 can be smaller font compare to #2

Address: 47 West Falcon Ridge Rd, Richmond Hill, ON L3K 2P9
Telephone: 416 730 4215
416 682 1947
Email: info@loftcraftas.ca

Back
Slogan: Convert plain room into designer’s interiors

Telephone: 416 730 4215
416 682 1947
Email: info@loftcraftas.ca

Images:
Front
1. Display our productions for crown mouldings, baseboards, casings and wainscotings, refer to our website www.loftcraftas.ca. (The winner finally we will provide the high resolution images, low resolution please copy from our website so far)
Back
2. Display 4-6 nice images for 1. wainscoting walls 2. feature walls, 3. waffle ceiling like attached below. BUT PLEASE DON'T USE THE IMAGES PROVIDED, THIS IS ONLY A SAMPLE. Please use high resolution images for printing. ALSO PLEASE DON'T LIMIT YOUR CREATIVITY TO USE 4 SQUARES LIKE BELOW IMAGES. Please provide more ideas

Note:
1. Please do the bleeding for final printing production
2. Images have to be high resolution for ready to print
3. Style need to be fresh, clean, easy to read, modern and magazine style
4. Information has to be readable, easy to find, front and back both need to display company address, telephone, email, you can use icon or abbreviation to do these information.

Thanks,
Loft Craftas

```html
<!DOCTYPE html>
<html lang="en">
<head>
<meta charset="utf-8">
<title>Loft Craftas Door Hanger</title>
<link href="https://fonts.googleapis.com/css2?family=Oswald:wght@500;600&family=Roboto+Condensed:wght@500;600&family=Lato:wght@400&display=swap" rel="stylesheet">
<style>
:root{
  --blue:#1f3f9c;
  --blue-deep:#142d7a;
  --orange:#f05a28;
  --ink:#3a434d;
  --slate:#56606a;
  --light:#f1f2f4;
  --stage:#d9d9d9;
  --white:#ffffff;
}
*{margin:0;padding:0;box-sizing:border-box}
html,body{width:1200px;height:2381px;overflow:hidden;background:var(--stage)}
.canvas{position:relative;width:1200px;height:2381px}
.hanger{position:absolute;top:449px;width:540px;height:1483px;overflow:hidden;box-shadow:0 6px 14px rgba(0,0,0,.25)}
.hanger--front{left:50px}
.hanger--back{left:610px}
.hanger svg.art{position:absolute;inset:0}
.layer{position:absolute;left:0;width:540px;text-align:center}
.brand{display:flex;align-items:center;justify-content:center;gap:16px}
.brand__square{width:44px;height:44px;background:var(--slate)}
.brand__name{font-family:'Lato',sans-serif;font-weight:400;color:var(--slate);letter-spacing:5px;text-transform:uppercase;white-space:nowrap}
.headline{font-family:'Oswald',sans-serif;font-weight:600;text-transform:uppercase;line-height:1}
.front-title__line{display:block;color:var(--ink);font-size:76px;letter-spacing:-1px;transform:scaleX(.92)}
.front-title__accent{display:block;color:var(--orange);font-size:100px;letter-spacing:-1px;transform:scaleX(.92)}
.intro{font-family:'Roboto Condensed',sans-serif;font-weight:600;color:var(--blue);font-size:22px;line-height:29px}
.service{font-family:'Oswald',sans-serif;font-weight:500;font-size:38px;letter-spacing:.5px;text-transform:uppercase}
.icons{display:flex;justify-content:center;gap:10px}
.icons svg{width:26px;height:26px}
.contact{font-family:'Roboto Condensed',sans-serif;font-weight:600;font-size:23px;line-height:31px;text-transform:uppercase}
.back-title{color:var(--white);font-size:88px;line-height:82px;letter-spacing:-1px}
.back-title span{display:block;transform:scaleX(.9)}
</style>
</head>
<body>
<div class="canvas">

  <!-- FRONT -->
  <section class="hanger hanger--front">
    <svg class="art" width="540" height="1483" viewBox="0 0 540 1483">
      <defs>
        <linearGradient id="roomTone" x1="0" y1="0" x2="0" y2="1">
          <stop offset="0" stop-color="#26262a"/><stop offset=".6" stop-color="#4a4547"/><stop offset="1" stop-color="#8a8784"/>
        </linearGradient>
        <linearGradient id="panelLight" x1="0" y1="0" x2="0" y2="1">
          <stop offset="0" stop-color="#ffffff"/><stop offset="1" stop-color="#e4e6ea"/>
        </linearGradient>
        <linearGradient id="blueFade" x1="0" y1="0" x2="0" y2="1">
          <stop offset="0" stop-color="#2447a8"/><stop offset="1" stop-color="#142d7a"/>
        </linearGradient>
        <radialGradient id="productTone" cx=".5" cy=".4" r=".6">
          <stop offset="0" stop-color="#ffffff"/><stop offset="1" stop-color="#d3d6da"/>
        </radialGradient>
      </defs>
      <rect x="0" y="0" width="540" height="640" fill="url(#roomTone)" role="img" aria-label="Living room photo with dark panelled wainscoting wall, two armchairs and side tables"/>
      <path d="M0 585 Q270 495 540 585 L540 660 L0 660 Z" fill="#b9c0c8"/>
      <path d="M0 598 Q270 512 540 598 L540 700 L0 700 Z" fill="var(--blue)"/>
      <path d="M0 625 Q270 548 540 625 L540 1483 L0 1483 Z" fill="url(#panelLight)"/>
      <line x1="60" y1="967" x2="480" y2="967" stroke="#d4d8dd" stroke-width="2"/>
      <path d="M0 1100 Q270 1060 540 1085 L540 1483 L0 1483 Z" fill="url(#blueFade)"/>
      <path d="M300 1170 Q430 1125 540 1098 L540 1140 Q440 1160 320 1200 Z" fill="var(--orange)"/>
      <rect x="0" y="1470" width="540" height="13" fill="var(--orange)"/>
      <g>
        <circle cx="100" cy="1148" r="75" fill="var(--white)" stroke="var(--blue)" stroke-width="6"/>
        <circle cx="100" cy="1148" r="63" fill="url(#productTone)" role="img" aria-label="Crown moulding product"/>
        <circle cx="268" cy="1163" r="75" fill="var(--white)" stroke="var(--blue)" stroke-width="6"/>
        <circle cx="268" cy="1163" r="63" fill="url(#productTone)" role="img" aria-label="Baseboard product"/>
        <circle cx="436" cy="1148" r="75" fill="var(--white)" stroke="var(--blue)" stroke-width="6"/>
        <circle cx="436" cy="1148" r="63" fill="url(#productTone)" role="img" aria-label="Casing product"/>
      </g>
      <line x1="180" y1="-10" x2="286" y2="128" stroke="var(--white)" stroke-width="34"/>
      <circle cx="286" cy="128" r="86" fill="var(--white)"/>
    </svg>

    <div class="layer brand" style="top:638px">
      <span class="brand__square"></span>
      <span class="brand__name" style="font-size:44px">Loft Craftas</span>
    </div>

    <h1 class="layer headline" style="top:708px">
      <span class="front-title__line">Moulding</span>
      <span class="front-title__line" style="margin-top:-2px">Factory Outlet</span>
      <span class="front-title__accent" style="margin-top:-4px">Direct Sale</span>
    </h1>

    <p class="layer intro" style="top:983px">Supply high quality Crown mouldings,<br>baseboards, casings and wainscotings<br>with competitive price</p>

    <p class="layer service" style="top:1245px;color:var(--white)">Installation &amp; Delivery</p>

    <div class="layer icons" style="top:1300px">
      <svg viewBox="0 0 26 26"><circle cx="13" cy="13" r="13" fill="var(--orange)"/><path d="M13 6a5 5 0 0 0-5 5c0 4 5 9 5 9s5-5 5-9a5 5 0 0 0-5-5zm0 7a2 2 0 1 1 0-4 2 2 0 0 1 0 4z" fill="var(--white)"/></svg>
      <svg viewBox="0 0 26 26"><circle cx="13" cy="13" r="13" fill="var(--orange)"/><path d="M9 7l3 3-2 2c1 2 2 3 4 4l2-2 3 3-2 2c-5 0-10-5-10-10z" fill="var(--white)"/></svg>
      <svg viewBox="0 0 26 26"><circle cx="13" cy="13" r="13" fill="var(--orange)"/><rect x="7" y="9" width="12" height="9" rx="1" fill="var(--white)"/><path d="M7 9l6 5 6-5" fill="none" stroke="var(--orange)" stroke-width="1.5"/></svg>
    </div>

    <p class="layer contact" style="top:1338px;color:var(--white)">47 West Falcon Ridge Rd,<br>Richmond Hill, ON L3K 2P9<br>416 730 4215 | 416 682 1947<br>info@loftcraftas.ca</p>
  </section>

  <!-- BACK -->
  <section class="hanger hanger--back">
    <svg class="art" width="540" height="1483" viewBox="0 0 540 1483">
      <defs>
        <linearGradient id="backLight" x1="0" y1="0" x2="1" y2="1">
          <stop offset="0" stop-color="#ffffff"/><stop offset=".5" stop-color="#eceef1"/><stop offset="1" stop-color="#dfe2e6"/>
        </linearGradient>
        <linearGradient id="roomBlue" x1="0" y1="0" x2="0" y2="1">
          <stop offset="0" stop-color="#1a3a98"/><stop offset=".55" stop-color="#1f3f9c"/><stop offset=".8" stop-color="#2b4aa4"/><stop offset="1" stop-color="#1a3890"/>
        </linearGradient>
        <radialGradient id="productToneB" cx=".5" cy=".4" r=".6">
          <stop offset="0" stop-color="#ffffff"/><stop offset="1" stop-color="#d3d6da"/>
        </radialGradient>
      </defs>
      <rect width="540" height="1483" fill="url(#backLight)"/>
      <path d="M0 405 Q270 335 540 420 L540 470 L0 470 Z" fill="#b9c0c8"/>
      <path d="M0 428 Q270 362 540 440 L540 900 Q300 850 0 880 Z" fill="url(#roomBlue)" role="img" aria-label="Living room interior photo tinted in blue, with sofa and framed wall panels"/>
      <path d="M0 975 Q300 950 540 900 L540 945 Q300 990 0 1000 Z" fill="var(--orange)"/>
      <line x1="60" y1="1225" x2="480" y2="1225" stroke="#d4d8dd" stroke-width="2"/>
      <g>
        <circle cx="97" cy="953" r="76" fill="var(--white)" stroke="var(--blue-deep)" stroke-width="6"/>
        <circle cx="97" cy="953" r="64" fill="url(#productToneB)" role="img" aria-label="Crown moulding product"/>
        <circle cx="267" cy="953" r="76" fill="var(--white)" stroke="var(--blue-deep)" stroke-width="6"/>
        <circle cx="267" cy="953" r="64" fill="url(#productToneB)" role="img" aria-label="Chair rail moulding product"/>
        <circle cx="437" cy="953" r="76" fill="var(--white)" stroke="var(--blue-deep)" stroke-width="6"/>
        <circle cx="437" cy="953" r="64" fill="url(#productToneB)" role="img" aria-label="Casing product"/>
        <circle cx="97" cy="1123" r="76" fill="var(--white)" stroke="var(--blue-deep)" stroke-width="6"/>
        <circle cx="97" cy="1123" r="64" fill="url(#productToneB)" role="img" aria-label="Baseboard product"/>
        <circle cx="267" cy="1123" r="76" fill="var(--white)" stroke="var(--blue-deep)" stroke-width="6"/>
        <circle cx="267" cy="1123" r="64" fill="url(#productToneB)" role="img" aria-label="Flatstock moulding product"/>
        <circle cx="437" cy="1123" r="76" fill="var(--white)" stroke="var(--blue-deep)" stroke-width="6"/>
        <circle cx="437" cy="1123" r="64" fill="url(#productToneB)" role="img" aria-label="Wainscoting cap product"/>
      </g>
      <line x1="180" y1="-10" x2="285" y2="128" stroke="var(--slate)" stroke-width="34"/>
      <circle cx="285" cy="128" r="86" fill="var(--slate)"/>
    </svg>

    <div class="layer brand" style="top:258px">
      <span class="brand__square" style="width:54px;height:54px"></span>
      <span class="brand__name" style="font-size:50px">Loft Craftas</span>
    </div>

    <h2 class="layer headline back-title" style="top:438px">
      <span>Convert</span>
      <span>Plain Room</span>
      <span>Into</span>
      <span>Designer’s</span>
      <span>Interiors</span>
    </h2>

    <p class="layer service" style="top:1243px;color:var(--orange)">Installation &amp; Delivery</p>

    <div class="layer icons" style="top:1297px">
      <svg viewBox="0 0 26 26"><circle cx="13" cy="13" r="13" fill="var(--orange)"/><path d="M13 6a5 5 0 0 0-5 5c0 4 5 9 5 9s5-5 5-9a5 5 0 0 0-5-5zm0 7a2 2 0 1 1 0-4 2 2 0 0 1 0 4z" fill="var(--white)"/></svg>
      <svg viewBox="0 0 26 26"><circle cx="13" cy="13" r="13" fill="var(--orange)"/><path d="M9 7l3 3-2 2c1 2 2 3 4 4l2-2 3 3-2 2c-5 0-10-5-10-10z" fill="var(--white)"/></svg>
      <svg viewBox="0 0 26 26"><circle cx="13" cy="13" r="13" fill="var(--orange)"/><rect x="7" y="9" width="12" height="9" rx="1" fill="var(--white)"/><path d="M7 9l6 5 6-5" fill="none" stroke="var(--orange)" stroke-width="1.5"/></svg>
    </div>

    <p class="layer contact" style="top:1335px;color:var(--blue)">47 West Falcon Ridge Rd,<br>Richmond Hill, ON L3K 2P9<br>416 730 4215 | 416 682 1947<br>info@loftcraftas.ca</p>
  </section>

</div>
</body>
</html>
```